Healthcare and Professional IT Services Company need a redesigned business card

We are a IT Services company that targets small medical practices and professional business such as Attorneys, Accounts, Architects etc. We want to communicate a professional yet friendly image using recent logo redesign here on ArtHarbor. Like to see the colors blue and orange in the design. Must use the Tall Pine Computing as displayed in the new logo - then also want to incorporate the fish logo as well.

Target Market(s)

Small medical and professional services

Industry/Entity Type

It Company

Contact Information for Business Card

The usual stuff, place for name address phone website. Also maybe our tagline which is "rooted in technology"

Requirements
Must have
• My new logo and the fish somewhere on the card

```html
<!DOCTYPE html>
<html lang="en">
<head>
<meta charset="utf-8">
<title>Tall Pine Computing – Business Card</title>
<link href="https://fonts.googleapis.com/css2?family=Quicksand:wght@400;500;700&display=swap" rel="stylesheet">
<style>
  :root {
    --page-bg: #e9eaec;
    --card-white: #f7f8f8;
    --brand-blue: #1593d1;
    --brand-blue-deep: #0d78b8;
    --brand-orange: #f2ae22;
    --text-light: #ffffff;
    --tagline-blue: #3d9fd4;
  }
  * { box-sizing: border-box; margin: 0; padding: 0; }
  html, body { width: 1200px; height: 780px; overflow: hidden; }
  body {
    background: var(--page-bg);
    font-family: "Quicksand", sans-serif;
    display: flex;
    align-items: center;
    justify-content: center;
    gap: 44px;
  }
  .card {
    width: 520px;
    height: 298px;
    border-radius: 4px;
    overflow: hidden;
    box-shadow: 0 6px 18px rgba(0,0,0,0.18);
    position: relative;
  }

  /* Front */
  .card-front { display: flex; flex-direction: column; background: var(--card-white); }
  .front-brand {
    height: 150px;
    display: flex;
    align-items: center;
    padding-left: 44px;
    gap: 20px;
  }
  .brand-mark {
    width: 62px; height: 62px; border-radius: 50%;
    flex: none;
  }
  .card-front .brand-mark { background: var(--brand-blue); }
  .brand-text { display: flex; flex-direction: column; gap: 6px; }
  .brand-name {
    font-weight: 700;
    font-size: 34px;
    line-height: 1;
    letter-spacing: -0.5px;
  }
  .card-front .brand-name { color: var(--brand-blue); }
  .tagline {
    font-weight: 400;
    font-size: 15px;
    letter-spacing: 3px;
  }
  .card-front .tagline { color: var(--tagline-blue); }

  .name-band {
    height: 32px;
    background: var(--brand-orange);
    display: flex;
    align-items: center;
    padding-left: 44px;
  }
  .employee-name {
    color: var(--text-light);
    font-weight: 700;
    font-size: 17px;
  }
  .contact-panel {
    flex: 1;
    background: linear-gradient(180deg, var(--brand-blue), var(--brand-blue-deep));
    color: var(--text-light);
    display: flex;
    align-items: center;
    padding: 0 30px 0 44px;
    font-size: 13px;
    font-weight: 500;
  }
  .contact-list { list-style: none; display: flex; flex-direction: column; gap: 5px; }
  .contact-list li { display: flex; align-items: center; gap: 8px; }
  .contact-icon {
    width: 14px; height: 14px; border-radius: 2px;
    background: var(--text-light);
    flex: none;
  }
  .contact-icon svg { display: block; }
  .contact-divider {
    width: 1px; height: 62px;
    background: rgba(255,255,255,0.8);
    margin: 0 18px;
  }
  .address { font-style: normal; line-height: 1.5; }

  /* Back */
  .card-back {
    background: radial-gradient(ellipse at 50% 45%, #1aa2dd 0%, var(--brand-blue) 45%, var(--brand-blue-deep) 100%);
    display: flex;
    align-items: center;
    justify-content: center;
    gap: 20px;
  }
  .card-back .brand-mark { background: var(--text-light); width: 70px; height: 70px; }
  .card-back .brand-name { color: var(--text-light); }
  .card-back .tagline { color: var(--text-light); }
</style>
</head>
<body>
  <section class="card card-front" aria-label="Business card front">
    <div class="front-brand">
      <div class="brand-mark" role="img" aria-label="Company mark"></div>
      <div class="brand-text">
        <span class="brand-name">Tall Pine Computing</span>
        <span class="tagline">rooted in technology</span>
      </div>
    </div>
    <div class="name-band">
      <span class="employee-name">Employee Name</span>
    </div>
    <div class="contact-panel">
      <ul class="contact-list">
        <li>
          <span class="contact-icon"><svg width="14" height="14" viewBox="0 0 14 14"><path d="M4 3 L6 5 L5 6.5 Q6.5 8.5 7.5 9 L9 8 L11 10 L9.5 11.5 Q5 10.5 2.5 4.5 Z" fill="#1593d1"/></svg></span>
          0123 456 789
        </li>
        <li>
          <span class="contact-icon"><svg width="14" height="14" viewBox="0 0 14 14"><rect x="3" y="5" width="8" height="5" fill="none" stroke="#1593d1" stroke-width="1.2"/><rect x="4.5" y="2.5" width="5" height="2.5" fill="#1593d1"/></svg></span>
          0123 456 789
        </li>
        <li>
          <span class="contact-icon"><svg width="14" height="14" viewBox="0 0 14 14"><rect x="2.5" y="4" width="9" height="6" fill="none" stroke="#1593d1" stroke-width="1.2"/><path d="M2.5 4 L7 7.5 L11.5 4" fill="none" stroke="#1593d1" stroke-width="1.2"/></svg></span>
          hello@tallpine.net.au
        </li>
      </ul>
      <div class="contact-divider"></div>
      <address class="address">
        P.O. Box 000<br>
        Cedar Hill, 2nd Lane, USA<br>
        www.yourwebsite.com
      </address>
    </div>
  </section>

  <section class="card card-back" aria-label="Business card back">
    <div class="brand-mark" role="img" aria-label="Company mark"></div>
    <div class="brand-text">
      <span class="brand-name">Tall Pine Computing</span>
      <span class="tagline">rooted in technology</span>
    </div>
  </section>
</body>
</html>
```